Tech business card design

We need an amazing business card design for our new business 'Pexla' a marketing tech startup based in Sydney, Australia. We provide an online marketplace for businesses to search and buy advertising media, connect with service providers and learn more about marketing. We wish to communicate 'cool tech', reliability and professionalism and design based around our logo.

Target Market(s)

Business Owners

Contact Information for Business Card

Name
Position
Email Address
Website
Phone Number

Font styles to use
Other font styles liked:
• Avenir & Avenir Next

Colors

Designer to choose colors to be used in the design.

```html
<!DOCTYPE html>
<html lang="en">
<head>
<meta charset="utf-8">
<title>Pexla Business Card</title>
<link rel="stylesheet" href="https://fonts.googleapis.com/css2?family=Roboto:wght@400;700;900&display=swap">
<style>
  :root {
    --stage: #1b1b1c;
    --navy: #13113a;
    --navy-soft: #1f1d52;
    --card-white: #f1f1f1;
    --card-shade: #e4e4e4;
    --ink: #16143f;
    --text-grey: #4a4a4f;
    --white: #ffffff;
  }
  * { margin: 0; padding: 0; box-sizing: border-box; }
  html, body {
    width: 1200px;
    height: 900px;
    overflow: hidden;
    background: var(--stage);
    font-family: "Roboto", sans-serif;
  }
  .canvas {
    position: relative;
    width: 1200px;
    height: 900px;
  }
  .card {
    position: absolute;
    left: 332px;
    width: 556px;
    height: 316px;
    box-shadow: 0 6px 14px rgba(0, 0, 0, 0.55);
  }
  .card-back {
    top: 134px;
    background: linear-gradient(135deg, var(--navy) 0%, var(--navy-soft) 50%, var(--navy) 100%);
    overflow: hidden;
  }
  .pattern-area {
    position: absolute;
    inset: 0;
    background: linear-gradient(135deg, var(--navy) 0%, var(--navy-soft) 55%, var(--navy) 100%);
  }
  .back-brand {
    position: absolute;
    right: 58px;
    bottom: 48px;
    font-weight: 900;
    font-size: 24px;
    color: var(--white);
    letter-spacing: -0.3px;
  }
  .card-front {
    top: 488px;
    background: linear-gradient(120deg, var(--card-shade) 0%, var(--card-white) 55%, #f6f6f6 100%);
  }
  .brand {
    position: absolute;
    left: 40px;
    top: 54px;
    font-weight: 900;
    font-size: 74px;
    line-height: 1;
    color: var(--ink);
    letter-spacing: -2px;
  }
  .contact-list {
    position: absolute;
    left: 42px;
    top: 223px;
    list-style: none;
  }
  .contact-item {
    display: flex;
    align-items: center;
    gap: 7px;
    font-size: 13.5px;
    color: var(--text-grey);
    height: 19px;
  }
  .contact-icon {
    width: 12px;
    height: 12px;
    fill: var(--ink);
  }
  .person {
    position: absolute;
    right: 48px;
    top: 224px;
    text-align: right;
  }
  .person-name {
    font-weight: 700;
    font-size: 24px;
    color: var(--ink);
    line-height: 1.1;
  }
  .person-role {
    font-size: 16px;
    color: var(--text-grey);
    line-height: 1.2;
  }
</style>
</head>
<body>
<main class="canvas">
  <section class="card card-back">
    <div class="pattern-area" role="img" aria-label="Navy background with a faint diagonal repeating brand-name pattern"></div>
    <span class="back-brand">Pexla</span>
  </section>

  <section class="card card-front">
    <h1 class="brand">Pexla</h1>

    <ul class="contact-list">
      <li class="contact-item">
        <svg class="contact-icon" viewBox="0 0 24 24" aria-hidden="true"><path d="M6.6 10.8a15.1 15.1 0 0 0 6.6 6.6l2.2-2.2a1 1 0 0 1 1-.25 11.4 11.4 0 0 0 3.6.57 1 1 0 0 1 1 1V20a1 1 0 0 1-1 1A17 17 0 0 1 3 4a1 1 0 0 1 1-1h3.5a1 1 0 0 1 1 1c0 1.25.2 2.45.57 3.57a1 1 0 0 1-.25 1z"/></svg>
        123 456 7890
      </li>
      <li class="contact-item">
        <svg class="contact-icon" viewBox="0 0 24 24" aria-hidden="true"><path d="M2 5h20v14H2z" opacity="0"/><path d="M3 5h18a1 1 0 0 1 1 1v1l-10 6L2 7V6a1 1 0 0 1 1-1zm-1 4.3 10 6 10-6V18a1 1 0 0 1-1 1H3a1 1 0 0 1-1-1z"/></svg>
        info@yourwebsite.com
      </li>
      <li class="contact-item">
        <svg class="contact-icon" viewBox="0 0 24 24" aria-hidden="true"><path d="M12 2a10 10 0 1 0 0 20 10 10 0 0 0 0-20zm6.9 6h-2.9a15.6 15.6 0 0 0-1.4-3.6A8 8 0 0 1 18.9 8zM12 4c.8 1.2 1.5 2.5 1.9 4h-3.8c.4-1.5 1.1-2.8 1.9-4zM4.3 14a8.2 8.2 0 0 1 0-4h3.4a16.5 16.5 0 0 0 0 4zm.8 2h2.9c.3 1.3.8 2.5 1.4 3.6A8 8 0 0 1 5.1 16zM8 8H5.1a8 8 0 0 1 4.3-3.6C8.8 5.5 8.3 6.7 8 8zm4 12c-.8-1.2-1.5-2.5-1.9-4h3.8c-.4 1.5-1.1 2.8-1.9 4zm2.3-6H9.7a14.7 14.7 0 0 1 0-4h4.6a14.7 14.7 0 0 1 0 4zm.3 5.6c.6-1.1 1.1-2.3 1.4-3.6h2.9a8 8 0 0 1-4.3 3.6zm1.7-5.6a16.5 16.5 0 0 0 0-4h3.4a8.2 8.2 0 0 1 0 4z"/></svg>
        www.yourwebsite.com
      </li>
    </ul>

    <div class="person">
      <p class="person-name">Marlon Vestry</p>
      <p class="person-role">Managing Director</p>
    </div>
  </section>
</main>
</body>
</html>
```